Calloway Metal Recyclers - www.callowayrecyclers-example.com.au

I've just rebranded my business and thought what better way to continue with this than getting a website.
It is going to be fairly basic for now. I've attached quite a few images, feel free to use whichever you like.
And pages description is also attached in a .doc file.
Updates

Hi, this is my first time having a website. I am open to anything and trust the experience and ideas you can bring forward. I will look at extending the deadline so I can take my time to give feedback as needed! Thank you all.

Target Market(s)

Mining and industrial and commercial sectors

Coding

Coded - Design and coding required

Number of Pages Required

5+ page

Requirements
Must have
• Logo/Phone number at the top of every page. "Scrap Metal Specialists" tag line at the top of every page.
Nice to have
• Top Navigation.

```html
<!DOCTYPE html>
<html lang="en">
<head>
<meta charset="utf-8">
<title>Calloway Metal Recyclers</title>
<link href="https://fonts.googleapis.com/css2?family=IBM+Plex+Sans:wght@400;500&family=Oswald:wght@500&display=swap" rel="stylesheet">
<style>
:root{
  --navy:#1b3a6d;
  --ink:#111;
  --grey-bg:#f5f5f5;
  --line:#e3e3e3;
  --text:#333;
  --muted:#8a8a8a;
  --brand-grey:#6f7276;
  --white:#fff;
  --black:#000;
}
*{box-sizing:border-box;margin:0;padding:0}
html,body{width:1200px;height:2969px;overflow:hidden}
body{position:relative;font-family:"IBM Plex Sans",sans-serif;color:var(--text);background:var(--white)}
a{text-decoration:none}
.abs{position:absolute}
.display{font-family:"Oswald",sans-serif;font-weight:500;text-transform:uppercase;letter-spacing:1.5px;color:var(--ink)}

.topbar{left:0;top:0;width:1200px;height:47px;background:var(--navy);color:var(--white);font-size:13px}
.topbar .item{top:14px;display:flex;align-items:center;gap:6px;white-space:nowrap}
.topbar .sep{top:8px;width:1px;height:28px;background:rgba(255,255,255,.6)}
.topbar .dot{width:9px;height:9px;border-radius:50%;background:var(--white);display:inline-block;margin-right:9px}

.navbar{left:0;top:47px;width:1200px;height:81px;background:var(--white);border-bottom:1px solid var(--line)}
.nav-link{top:32px;font-size:15.5px;color:var(--text)}
.nav-active{left:451px;top:124px;width:32px;height:3px;background:var(--navy)}
.brand-badge{left:150px;top:0;width:174px;height:174px;border-radius:50%;background:var(--white);display:flex;flex-direction:column;align-items:center;justify-content:center;text-align:center;z-index:2}
.brand-name{font-family:"Oswald",sans-serif;font-weight:500;text-transform:uppercase;font-size:24px;line-height:26px;color:var(--brand-grey);width:140px}
.brand-tag{margin-top:6px;font-size:10.5px;letter-spacing:.5px;text-transform:uppercase;color:var(--navy);font-weight:500}
.brand-phone{font-size:12px;color:var(--brand-grey);margin-top:2px}

.hero{left:0;top:128px;width:1200px;height:686px;background:linear-gradient(160deg,#4a4d52 0%,#2a2c30 40%,#191a1c 75%,#3a3b2a 100%)}
.hero-title{left:0;top:200px;width:1200px;text-align:center;color:var(--white);font-size:50px;line-height:60px}
.hero-text{left:294px;top:334px;width:596px;text-align:center;color:var(--white);font-size:14.5px;line-height:26px}
.btn{display:flex;align-items:center;justify-content:center;background:var(--navy);color:var(--white);font-family:"Oswald",sans-serif;font-weight:500;text-transform:uppercase;font-size:16px;letter-spacing:1px;border-radius:30px 4px 4px 30px}

.services{left:0;top:814px;width:1200px;height:771px}
.vline{left:595px;top:0;width:1px;height:771px;background:var(--line)}
.hline{left:0;top:300px;width:1200px;height:1px;background:var(--line)}
.svc-icon{background:var(--navy);border-radius:10px;opacity:.9}
.svc-title{font-size:24px;line-height:37px}

.about{left:0;top:1585px;width:1200px;height:525px;background:var(--grey-bg)}
.about p{font-size:15.5px;line-height:26px;color:var(--text)}

.contact-title{left:0;top:2168px;width:1200px;text-align:center;font-size:34px}
.info-circle{width:50px;height:50px;border:2px solid var(--navy);border-radius:50%;display:flex;align-items:center;justify-content:center}
.info-label{font-size:17px}
.info-text{font-size:15.5px;line-height:25px;color:var(--text)}
.field{background:var(--white);box-shadow:0 4px 14px rgba(0,0,0,.07);font-size:15px;color:var(--muted);padding:14px 24px}

.footer{left:0;top:2617px;width:1200px;height:352px;background:var(--black);color:var(--white)}
.footer .display{color:var(--white)}
.foot-head{font-size:19px}
.foot-text{font-size:15.5px;line-height:25px;color:var(--white)}
.social{width:32px;height:32px;border-radius:50%;background:var(--white)}
.foot-rule{left:112px;top:262px;width:976px;height:1px;background:#2d2d2d}
.copy{left:0;top:296px;width:1200px;text-align:center;font-size:15px}
</style>
</head>
<body>

<header>
  <div class="abs topbar">
    <div class="abs item" style="left:418px">
      <svg width="12" height="12" viewBox="0 0 24 24"><path fill="#fff" d="M6.6 10.8a15 15 0 0 0 6.6 6.6l2.2-2.2a1 1 0 0 1 1-.25 11.4 11.4 0 0 0 3.6.57 1 1 0 0 1 1 1V20a1 1 0 0 1-1 1A17 17 0 0 1 3 4a1 1 0 0 1 1-1h3.5a1 1 0 0 1 1 1c0 1.25.2 2.45.57 3.57a1 1 0 0 1-.25 1z"/></svg>
      +61 8 5550 0100</div>
    <div class="abs sep" style="left:567px"></div>
    <div class="abs item" style="left:589px">
      <svg width="13" height="11" viewBox="0 0 24 20"><rect x="1" y="1" width="22" height="18" rx="2" fill="#fff"/><path d="M2 3l10 8 10-8" stroke="#1b3a6d" stroke-width="2" fill="none"/></svg>
      info@calloway-example.com.au</div>
    <div class="abs sep" style="left:846px"></div>
    <div class="abs item" style="left:882px">
      <svg width="12" height="12" viewBox="0 0 24 24"><path fill="#fff" d="M10 17l5-5-5-5v3H2v4h8zM14 3h6a2 2 0 0 1 2 2v14a2 2 0 0 1-2 2h-6v-2h6V5h-6z"/></svg>
      Login</div>
    <div class="abs sep" style="left:971px"></div>
    <div class="abs item" style="left:1003px;top:18px"><span class="dot"></span><span class="dot"></span><span class="dot"></span><span class="dot"></span></div>
  </div>

  <nav class="abs navbar">
    <a class="abs nav-link" style="left:451px">Home</a>
    <a class="abs nav-link" style="left:546px">About</a>
    <a class="abs nav-link" style="left:642px">Our Services</a>
    <a class="abs nav-link" style="left:784px">Online Store</a>
    <a class="abs nav-link" style="left:925px">Blog</a>
    <a class="abs nav-link" style="left:1010px">Contact Us</a>
  </nav>
  <div class="abs nav-active"></div>
  <div class="abs brand-badge">
    <span class="brand-name">Calloway Metal Recyclers</span>
    <span class="brand-tag">Scrap Metal Specialists</span>
    <span class="brand-phone">0400555019</span>
  </div>
</header>

<section class="abs hero" role="img" aria-label="Photo of a conveyor belt carrying crushed ore between yellow safety rails">
  <h1 class="abs display hero-title" style="color:#fff">Welcome to<br>Calloway Metal Recyclers</h1>
  <p class="abs hero-text">Welcome to the website of Calloway Metal Recyclers. We are a Perth based company that provides scrap metal collection and oxy cutting services in the mining, construction, and industrial sectors all around WA.</p>
  <a class="abs btn" style="left:507px;top:423px;width:170px;height:53px">Get Started</a>
</section>

<section class="abs services">
  <div class="abs vline"></div>
  <div class="abs hline"></div>
  <h2 class="abs display" style="left:197px;top:120px;font-size:42px;line-height:56px">Our<br>Services</h2>

  <div class="abs svc-icon" style="left:670px;top:92px;width:75px;height:75px" role="img" aria-label="Icon of a pickaxe breaking rock"></div>
  <h3 class="abs display svc-title" style="left:672px;top:190px;width:320px">Oxy cutting and breaking down of:</h3>

  <div class="abs svc-icon" style="left:194px;top:343px;width:92px;height:80px" role="img" aria-label="Icon of a mining haul truck"></div>
  <h3 class="abs display svc-title" style="left:194px;top:441px;width:370px">Large mining machinery - up to 800T excavators, haul packs, loaders, buckets, booms</h3>

  <div class="abs svc-icon" style="left:665px;top:333px;width:118px;height:77px" role="img" aria-label="Icon of a conveyor belt with a crate"></div>
  <h3 class="abs display svc-title" style="left:663px;top:440px;width:390px">Large minesite infrastructure - tanks, conveyors, crushers, SAG\ and ball mills</h3>

  <a class="abs btn" style="left:511px;top:605px;width:170px;height:54px">View More</a>
</section>

<section class="abs about">
  <svg class="abs" style="left:0;top:0" width="620" height="525" role="img" aria-label="Photo of a welder cutting steel with blue sparks">
    <defs>
      <radialGradient id="weld" cx="0.55" cy="0.5" r="0.7">
        <stop offset="0" stop-color="#5d8fd0"/>
        <stop offset="0.35" stop-color="#1e3f73"/>
        <stop offset="1" stop-color="#0b1424"/>
      </radialGradient>
    </defs>
    <path d="M0 0H353A262 262 0 0 1 353 525H0Z" fill="url(#weld)"/>
  </svg>
  <h2 class="abs display" style="left:673px;top:110px;font-size:34px">About Us</h2>
  <p class="abs" style="left:673px;top:185px;width:410px">My name is Dale Calloway and I’m the managing director of Calloway Metal Processors. I have been in the scrap metal recycling industry longer than I haven’t! I have 16 years’ experience in everything scrap metal and I am very passionate about sustainable recycling</p>
  <a class="abs btn" style="left:667px;top:332px;width:170px;height:53px">Learn More</a>
</section>

<section>
  <h2 class="abs display contact-title">Contact Us</h2>

  <div class="abs info-circle" style="left:118px;top:2277px">
    <svg width="14" height="16" viewBox="0 0 24 28"><path fill="#1b3a6d" d="M12 0a10 10 0 0 0-10 10c0 7.5 10 18 10 18s10-10.5 10-18A10 10 0 0 0 12 0zm0 14a4 4 0 1 1 0-8 4 4 0 0 1 0 8z"/></svg>
  </div>
  <div class="abs display info-label" style="left:182px;top:2274px">Location</div>
  <p class="abs info-text" style="left:182px;top:2304px;width:240px">Dale Calloway United State dolor sit amet,</p>

  <div class="abs info-circle" style="left:118px;top:2382px">
    <svg width="14" height="14" viewBox="0 0 24 24"><path fill="#1b3a6d" d="M6.6 10.8a15 15 0 0 0 6.6 6.6l2.2-2.2a1 1 0 0 1 1-.25 11.4 11.4 0 0 0 3.6.57 1 1 0 0 1 1 1V20a1 1 0 0 1-1 1A17 17 0 0 1 3 4a1 1 0 0 1 1-1h3.5a1 1 0 0 1 1 1c0 1.25.2 2.45.57 3.57a1 1 0 0 1-.25 1z"/></svg>
  </div>
  <div class="abs display info-label" style="left:182px;top:2379px">Phone</div>
  <p class="abs info-text" style="left:183px;top:2409px">0400555019</p>

  <div class="abs info-circle" style="left:118px;top:2477px">
    <svg width="14" height="12" viewBox="0 0 24 20"><rect x="1" y="1" width="22" height="18" rx="2" fill="#1b3a6d"/><path d="M2 3l10 8 10-8" stroke="#fff" stroke-width="2" fill="none"/></svg>
  </div>
  <div class="abs display info-label" style="left:182px;top:2474px">Email</div>
  <p class="abs info-text" style="left:183px;top:2504px;width:240px">dale@calloway-example.com.au</p>

  <div class="abs field" style="left:441px;top:2277px;width:318px;height:52px">Name</div>
  <div class="abs field" style="left:441px;top:2344px;width:318px;height:52px">Phone</div>
  <div class="abs field" style="left:441px;top:2412px;width:318px;height:52px">Email</div>
  <a class="abs btn" style="left:441px;top:2481px;width:318px;height:53px;border-radius:0;font-size:15px">Send</a>
  <div class="abs field" style="left:779px;top:2277px;width:300px;height:257px">Type your message</div>
</section>

<footer class="abs footer">
  <div class="abs display" style="left:110px;top:46px;width:220px;font-size:30px;line-height:36px">Calloway Metal Recyclers</div>
  <div class="abs" style="left:110px;top:160px;font-size:13px;letter-spacing:.5px;text-transform:uppercase;color:#fff">Scrap Metal Specialists</div>

  <h4 class="abs display foot-head" style="left:430px;top:56px">Contact Us</h4>
  <svg class="abs" style="left:433px;top:112px" width="10" height="13" viewBox="0 0 24 28"><path fill="#fff" d="M12 0a10 10 0 0 0-10 10c0 7.5 10 18 10 18s10-10.5 10-18A10 10 0 0 0 12 0zm0 14a4 4 0 1 1 0-8 4 4 0 0 1 0 8z"/></svg>
  <p class="abs foot-text" style="left:453px;top:106px;width:230px">Dale Calloway United State dolor sit amet,</p>
  <svg class="abs" style="left:433px;top:170px" width="12" height="12" viewBox="0 0 24 24"><path fill="#fff" d="M6.6 10.8a15 15 0 0 0 6.6 6.6l2.2-2.2a1 1 0 0 1 1-.25 11.4 11.4 0 0 0 3.6.57 1 1 0 0 1 1 1V20a1 1 0 0 1-1 1A17 17 0 0 1 3 4a1 1 0 0 1 1-1h3.5a1 1 0 0 1 1 1c0 1.25.2 2.45.57 3.57a1 1 0 0 1-.25 1z"/></svg>
  <p class="abs foot-text" style="left:454px;top:164px">0400555019</p>
  <svg class="abs" style="left:432px;top:207px" width="15" height="12" viewBox="0 0 24 20"><rect x="1" y="1" width="22" height="18" rx="2" fill="#fff"/><path d="M2 3l10 8 10-8" stroke="#000" stroke-width="2" fill="none"/></svg>
  <p class="abs foot-text" style="left:455px;top:201px">dale@calloway-example.com.au</p>

  <h4 class="abs display foot-head" style="left:724px;top:56px">Help Link</h4>
  <p class="abs foot-text" style="left:727px;top:96px">Terms &amp; Conditions</p>
  <p class="abs foot-text" style="left:727px;top:126px">Privacy Policy</p>
  <p class="abs foot-text" style="left:727px;top:156px">About Us</p>
  <p class="abs foot-text" style="left:727px;top:186px">Support</p>

  <h4 class="abs display foot-head" style="left:941px;top:56px">Follow Us</h4>
  <div class="abs social" style="left:940px;top:100px"></div>
  <div class="abs social" style="left:979px;top:100px"></div>
  <div class="abs social" style="left:1018px;top:100px"></div>
  <div class="abs social" style="left:1056px;top:100px"></div>

  <div class="abs foot-rule"></div>
  <p class="abs copy">©Copyrights 2022 Calloway Metal Recyclers | All rights reserved</p>
</footer>

</body>
</html>
```